Hartwell Estates Business Cards

I would like a business card that includes myself and my partner.
Includes: Logo, office #, email, website, our names, our numbers and possibly the address. I would also like the logo to be embossed and the card to be horizontal.
There is a photo of our yard signs to give you an idea of the colors of our business.

Target Market(s)

Everyone in real estate market.
We are in a rural area. Our clientele are from all socioeconomic backgrounds.

Industry/Entity Type

Real Estate Agent

Contact Information for Business Card

Company Name: Hartwell Estates
Our Names, Titles & Cell #'s : Dana Pembrook-Broker (555).317.6624, Marla Pembrook-Realtor (555).609.1385
Office #: (555).240.3918
Website: hartwellestates-demo.com
Joint Email: pembrook@hartwellestates-demo.com
Office Address: 418B W. Calloway Ave.
Millbrook, TX. 70913

Font styles to use
Serif

Requirements
Must have
• HORIZONTAL, Logo, Myself and my partners names, Our cell #'s, our office #, our website, our email address
Nice to have
• Embossed logo, office address, our titles.

```html
<!DOCTYPE html>
<html lang="en">
<head>
<meta charset="utf-8">
<title>Hartwell Estates Business Cards</title>
<link rel="stylesheet" href="https://fonts.googleapis.com/css2?family=EB+Garamond:wght@600&family=Source+Sans+3:wght@400;600&display=swap">
<style>
  :root {
    --backdrop: #1c1c1c;
    --card: #ffffff;
    --brand-purple: #3b1a5a;
    --ink: #2a2a2a;
  }
  html, body {
    margin: 0;
    width: 1200px;
    height: 900px;
    overflow: hidden;
    background: var(--backdrop);
  }
  .stage {
    position: relative;
    width: 1200px;
    height: 900px;
  }
  .card {
    position: absolute;
    top: 306px;
    width: 440px;
    height: 271px;
    background: var(--card);
    border-radius: 10px;
    overflow: hidden;
  }
  .card--front { left: 149px; }
  .card--back { left: 608px; }

  .brand-mark {
    position: absolute;
    display: flex;
    align-items: center;
    gap: 12px;
    font-family: "EB Garamond", serif;
    font-weight: 600;
    color: var(--brand-purple);
  }
  .brand-mark__dot {
    flex: none;
    border-radius: 50%;
    background: var(--brand-purple);
  }
  .card--front .brand-mark {
    left: 22px;
    top: 60px;
    width: 180px;
    flex-direction: column;
    text-align: center;
    font-size: 34px;
    line-height: 1.05;
  }
  .card--front .brand-mark__dot { width: 54px; height: 54px; }
  .card--back .brand-mark {
    left: 0;
    right: 0;
    top: 112px;
    justify-content: center;
    font-size: 38px;
    line-height: 1;
  }
  .card--back .brand-mark__dot { width: 40px; height: 40px; }

  .contact {
    position: absolute;
    left: 217px;
    top: 32px;
    font-family: "Source Sans 3", sans-serif;
    color: var(--ink);
    font-size: 12px;
    line-height: 16px;
  }
  .person + .person { margin-top: 12px; }
  .person__name {
    font-size: 15px;
    font-weight: 600;
    color: var(--brand-purple);
    line-height: 18px;
  }
  .person__title { line-height: 15px; }
  .line {
    display: flex;
    align-items: center;
    gap: 5px;
    height: 16px;
  }
  .line svg { width: 10px; height: 10px; fill: var(--brand-purple); flex: none; }
  .line--email { letter-spacing: -0.3px; }
  .address { margin-top: 8px; line-height: 16px; }
  .office { margin-top: 9px; }
</style>
</head>
<body>
<main class="stage">
  <section class="card card--front">
    <div class="brand-mark">
      <span class="brand-mark__dot"></span>
      <span>Hartwell<br>Estates</span>
    </div>
    <div class="contact">
      <div class="person">
        <div class="person__name">Dana Pembrook</div>
        <div class="person__title">Broker</div>
        <div class="line">
          <svg viewBox="0 0 10 10"><path d="M2 0.5 L3.6 2.8 L2.7 3.8 Q3.8 6 6.2 7.3 L7.2 6.4 L9.5 8 L8.2 9.5 Q4.3 9 0.5 2 Z"/></svg>
          <span>(555).317.6624</span>
        </div>
      </div>
      <div class="person">
        <div class="person__name">Marla Pembrook</div>
        <div class="person__title">Realtor</div>
        <div class="line">
          <svg viewBox="0 0 10 10"><path d="M2 0.5 L3.6 2.8 L2.7 3.8 Q3.8 6 6.2 7.3 L7.2 6.4 L9.5 8 L8.2 9.5 Q4.3 9 0.5 2 Z"/></svg>
          <span>(555).609.1385</span>
        </div>
      </div>
      <div class="address">418B W. Calloway Ave.<br>Millbrook, TX. 70913</div>
      <div class="office">
        <div class="line">
          <svg viewBox="0 0 10 10"><path d="M2 0.5 L3.6 2.8 L2.7 3.8 Q3.8 6 6.2 7.3 L7.2 6.4 L9.5 8 L8.2 9.5 Q4.3 9 0.5 2 Z"/></svg>
          <span>(555).240.3918</span>
        </div>
        <div class="line line--email">
          <svg viewBox="0 0 10 10"><path d="M1 2.5 H9 V7.5 H1 Z M1 2.5 L5 5.5 L9 2.5" fill="var(--brand-purple)" stroke="#fff" stroke-width="0.8"/></svg>
          <span>pembrook@hartwellestates-demo.com</span>
        </div>
        <div class="line">
          <svg viewBox="0 0 10 10"><circle cx="5" cy="5" r="4.5"/><path d="M0.5 5 H9.5 M5 0.5 Q2.5 5 5 9.5 M5 0.5 Q7.5 5 5 9.5" fill="none" stroke="#fff" stroke-width="0.7"/></svg>
          <span>hartwellestates-demo.com</span>
        </div>
      </div>
    </div>
  </section>

  <section class="card card--back">
    <div class="brand-mark">
      <span class="brand-mark__dot"></span>
      <span>Hartwell Estates</span>
    </div>
  </section>
</main>
</body>
</html>
```